Front and content page design for Fitness Cookbook

I am looking for someone to Design a front cover for a Recipe book and also create an amazing layout for the book.

Its for a corporate seminar so has to be eye catching, professional and bold.

Content is complete

Target Market(s)

Industry/Entity Type

Health And Wellness

Font styles to use
Sans Serif

Requirements
Must have
• Eye catching, professional and bold.
• By Dorian as stated on the document
• Must have Tidewell Motion Logo on it.

```html
<!DOCTYPE html>
<html lang="en">
<head>
<meta charset="utf-8">
<title>Chocolate Chip Cookies – Recipe Page</title>
<link rel="stylesheet" href="https://fonts.googleapis.com/css2?family=Lato:wght@400;700&display=swap">
<style>
  :root {
    --brand-orange: #f39a1e;
    --ink: #2b2b2b;
    --paper: #ffffff;
    --photo-dark: #6f6b68;
    --photo-light: #b9b5b1;
    --photo-warm: #c99d6a;
  }
  * { margin: 0; padding: 0; box-sizing: border-box; }
  html, body { width: 849px; height: 1200px; overflow: hidden; background: var(--paper); }
  .recipe-page {
    position: relative;
    width: 849px;
    height: 1200px;
    background: var(--paper);
    font-family: "Lato", sans-serif;
    color: var(--ink);
  }
  .dish-photo {
    position: absolute;
    left: 0; top: 0;
    width: 849px; height: 523px;
    background:
      radial-gradient(ellipse 38% 30% at 48% 52%, var(--photo-warm) 0%, #d8c2a2 55%, transparent 80%),
      radial-gradient(ellipse 70% 60% at 50% 55%, #f1efec 0%, #dcd9d6 55%, transparent 75%),
      linear-gradient(160deg, var(--photo-dark), var(--photo-light));
  }
  .title-band {
    position: absolute;
    left: 0; top: 523px;
    width: 849px; height: 136px;
    background: var(--brand-orange);
    display: flex;
    align-items: center;
    justify-content: center;
  }
  .recipe-title {
    color: var(--paper);
    font-weight: 400;
    font-size: 50px;
    letter-spacing: 0.5px;
  }
  .recipe-body {
    position: absolute;
    left: 51px; top: 674px;
    width: 750px;
    font-size: 16px;
    line-height: 21px;
  }
  .timing { margin-bottom: 21px; }
  .label, .section-heading {
    color: var(--brand-orange);
    font-weight: 700;
    text-transform: uppercase;
    font-size: 17px;
  }
  .section-heading { margin-bottom: 2px; }
  .ingredient-list { list-style: none; margin-bottom: 23px; }
  .method p { margin: 0; }
  .page-footer {
    position: absolute;
    right: 32px; bottom: 42px;
    display: flex;
    align-items: center;
    gap: 8px;
    font-size: 14px;
  }
  .brand-mark {
    width: 14px; height: 14px;
    border-radius: 50%;
    background: var(--brand-orange);
  }
  .brand-name { color: var(--ink); font-weight: 400; margin-right: 10px; }
  .page-number { font-weight: 400; }
</style>
</head>
<body>
<main class="recipe-page">
  <div class="dish-photo" role="img" aria-label="Photo of oat chocolate chip cookies on a white plate"></div>

  <header class="title-band">
    <h1 class="recipe-title">Chocolate Chip Cookies</h1>
  </header>

  <section class="recipe-body">
    <div class="timing">
      <div><span class="label">Prep time</span> 10 mins</div>
      <div><span class="label">Cooking time</span> 10 mins</div>
    </div>

    <h2 class="section-heading">Ingredients</h2>
    <ul class="ingredient-list">
      <li>1 cup oat flour (oats blended)</li>
      <li>3/4 cup natural Greek yoghurt</li>
      <li>2 egg whites</li>
      <li>1/2 tsp vanilla essence</li>
      <li>1 tsp baking powder</li>
      <li>1/2 tsp salt</li>
      <li>1/2 cup organic dark chocolate chips</li>
    </ul>

    <h2 class="section-heading">Cooking instructions</h2>
    <div class="method">
      <p>Mix dry ingredients (oat flour, baking powder and salt) together and mix wet ingredients (yoghurt, egg whites and vanilla) separately.</p>
      <p>Combine together in one bowl and stir in chocolate chips. Dollop the batter onto a baking try in 8-12 circles. Bake for 8-10 minutes at 190°C BUT keep an eye on them so they don't burn! Leave to cool for 5 minutes before eating.</p>
    </div>
  </section>

  <footer class="page-footer">
    <span class="brand-mark"></span>
    <span class="brand-name">Tidewell Motion</span>
    <span class="page-number">35</span>
  </footer>
</main>
</body>
</html>
```